BildeVOLD buisnesscard

Hey :) I need a modern buisnesscard for my company BildeVOLD
It most have:
Dagligleder og Fotograf: Henrik Audun Strandvik

Mob: +4791264085
Epost: post@bildevold.example
Adresse: Kvernbakken9, 6040 Langevåg

Facbook and instagram logo with text BildeVOLD

BildeVOLD logo

It Company

```html
<!DOCTYPE html>
<html lang="no">
<head>
<meta charset="utf-8">
<title>BildeVOLD – visittkort</title>
<link href="https://fonts.googleapis.com/css2?family=Open+Sans:wght@400;700&display=swap" rel="stylesheet">
<style>
  :root {
    --backdrop: #e9e6e1;
    --card-dark: #0d0d0d;
    --card-dark-tone: #1a1a1a;
    --card-light: #c4c4c4;
    --ink: #111111;
    --ink-soft: #1c1c1c;
    --logo-grey: #c9c9c9;
  }
  * { box-sizing: border-box; margin: 0; padding: 0; }
  html, body {
    width: 1200px;
    height: 900px;
    overflow: hidden;
    background: var(--backdrop);
    font-family: "Open Sans", Arial, sans-serif;
  }
  .sheet {
    position: relative;
    width: 1200px;
    height: 900px;
    display: flex;
    align-items: center;
    justify-content: center;
    gap: 60px;
  }
  .card {
    position: relative;
    width: 525px;
    height: 300px;
    border-radius: 3px;
    box-shadow: 0 6px 18px rgba(0,0,0,0.18);
    overflow: hidden;
  }

  /* Front side */
  .card--front {
    background: linear-gradient(135deg, var(--card-dark-tone) 0%, var(--card-dark) 60%);
    display: flex;
    align-items: center;
    justify-content: center;
  }
  .front-brand {
    display: flex;
    flex-direction: column;
    align-items: center;
    gap: 18px;
  }
  .front-brand__mark {
    width: 64px;
    height: 64px;
    background: var(--logo-grey);
  }
  .front-brand__name {
    color: var(--logo-grey);
    font-weight: 700;
    font-size: 54px;
    letter-spacing: 0.5px;
    line-height: 1;
  }

  /* Back side */
  .card--back {
    background: var(--card-light);
    display: grid;
    grid-template-columns: 235px 1fr;
    align-items: center;
  }
  .back-brand {
    display: flex;
    flex-direction: column;
    align-items: center;
    gap: 14px;
  }
  .back-brand__mark {
    width: 88px;
    height: 88px;
    background: var(--ink);
  }
  .back-brand__name {
    color: var(--ink);
    font-weight: 700;
    font-size: 26px;
    line-height: 1;
  }
  .contact {
    color: var(--ink-soft);
    font-size: 12.5px;
    line-height: 1.45;
    padding-right: 20px;
  }
  .contact__name {
    font-weight: 700;
    font-size: 14px;
    margin-bottom: 16px;
  }
  .contact__row {
    display: flex;
    align-items: center;
    gap: 8px;
  }
  .contact__row svg { width: 10px; height: 10px; flex: none; }
  .contact__address { margin-top: 14px; margin-bottom: 14px; }
  .social {
    display: flex;
    align-items: center;
    gap: 7px;
    font-size: 13px;
    margin-top: 4px;
    padding-left: 18px;
  }
  .social__dot {
    width: 14px;
    height: 14px;
    border-radius: 3px;
    background: var(--ink);
    flex: none;
  }
</style>
</head>
<body>
<main class="sheet">
  <section class="card card--front" aria-label="Forside">
    <div class="front-brand">
      <span class="front-brand__mark" aria-hidden="true"></span>
      <span class="front-brand__name">BildeVOLD</span>
    </div>
  </section>

  <section class="card card--back" aria-label="Bakside">
    <div class="back-brand">
      <span class="back-brand__mark" aria-hidden="true"></span>
      <span class="back-brand__name">BildeVOLD</span>
    </div>
    <div class="contact">
      <p class="contact__name">Henrik Audun Strandvik</p>
      <p class="contact__row">
        <svg viewBox="0 0 10 10" aria-hidden="true"><path d="M1 3.2C1 2 2 1.5 5 1.5S9 2 9 3.2L7.4 4 7 3H3L2.6 4ZM2.5 4.5h5L9 8.5H1Z" fill="#111"/></svg>
        +4791264085
      </p>
      <p class="contact__row">
        <svg viewBox="0 0 10 10" aria-hidden="true"><rect x="0.5" y="2" width="9" height="6.5" fill="#111"/><path d="M0.8 2.3 5 5.6 9.2 2.3" stroke="#c4c4c4" stroke-width="0.9" fill="none"/></svg>
        post@bildevold.example
      </p>
      <p class="contact__address">Kvernbakken9, 6040 Langevåg</p>
      <p class="social"><span class="social__dot" aria-hidden="true"></span>BildeVOLD</p>
      <p class="social"><span class="social__dot" aria-hidden="true"></span>BildeVOLD</p>
    </div>
  </section>
</main>
</body>
</html>
```